Local Roofing/Construction company business needs new biz card design

We need a new business card design, current cards are from the start of this operation and generic at best. We are a local Construction Company (General Contractor) with a majority of our work originating from insurance claims-exterior finish work is the main focus (Roofs-Siding-Gutters etc). Heavily involved with homeowners and the low ball offers they receive from insurance company's after a insurable event takes place. I have attached some of our original logo file(s) below.

```html
<!DOCTYPE html>
<html lang="en">
<head>
<meta charset="UTF-8">
<title>Northcrest Construction – Business Card</title>
<link href="https://fonts.googleapis.com/css2?family=Montserrat:wght@400;500;600;700;800&display=swap" rel="stylesheet">
<style>
  :root {
    --green: #4cb96b;
    --green-deep: #3fae5f;
    --ink: #1b1b1b;
    --black: #111412;
    --paper: #ffffff;
    --backdrop: #2a2b2e;
  }
  * { margin: 0; padding: 0; box-sizing: border-box; }
  html, body {
    width: 1200px; height: 900px; overflow: hidden;
    background: var(--backdrop);
    font-family: "Montserrat", sans-serif;
  }
  .stage {
    position: relative; width: 1200px; height: 900px;
  }
  .card {
    position: absolute; left: 320px;
    width: 560px; height: 320px;
    border-radius: 18px; overflow: hidden;
  }
  .card--back { top: 100px; }
  .card--front { top: 480px; background: var(--paper); }

  /* Back */
  .back-pattern {
    position: absolute; inset: 0;
    background: var(--green);
  }
  .back-brand {
    position: absolute; left: 50%; top: 50%;
    transform: translate(-50%, -50%);
    display: flex; align-items: center; gap: 10px;
    color: var(--paper);
    font-weight: 800; font-size: 15px; letter-spacing: 1px;
    text-transform: uppercase;
  }
  .back-brand .mark-square {
    width: 22px; height: 22px; background: var(--paper); border-radius: 3px;
  }

  /* Front */
  .brand {
    position: absolute; left: 150px; top: 48px;
    display: flex; align-items: center; gap: 12px;
    color: var(--ink);
  }
  .brand .mark-square {
    width: 34px; height: 34px; background: var(--green);
  }
  .brand-name {
    font-weight: 800; font-size: 22px; line-height: 1.05;
    text-transform: uppercase; letter-spacing: 0.5px;
  }
  .person {
    position: absolute; left: 40px; top: 158px;
  }
  .person-name {
    color: var(--green); font-weight: 700; font-size: 24px;
  }
  .person-title {
    color: var(--ink); font-weight: 500; font-size: 13px; margin-top: 2px; margin-left: 40px;
  }
  .divider {
    position: absolute; left: 258px; top: 126px;
    width: 2px; height: 96px; background: var(--green);
  }
  .contact {
    position: absolute; left: 276px; top: 120px;
    color: var(--ink); font-size: 11.5px; font-weight: 500; line-height: 1.35;
  }
  .contact-address { margin-bottom: 10px; }
  .contact-list { list-style: none; }
  .contact-list li {
    display: flex; align-items: center; gap: 10px; height: 17px;
  }
  .contact-list svg { width: 11px; height: 11px; flex: none; fill: var(--green); }
  .footer-bands {
    position: absolute; left: 0; bottom: 0; width: 560px; height: 320px;
  }
</style>
</head>
<body>
<main class="stage">

  <section class="card card--back" aria-label="Card back">
    <div class="back-pattern" role="img" aria-label="Green background with a repeating tonal brand pattern"></div>
    <div class="back-brand"><span class="mark-square"></span>Northcrest</div>
  </section>

  <section class="card card--front" aria-label="Card front">
    <div class="brand">
      <span class="mark-square"></span>
      <div class="brand-name">Northcrest<br>Construction</div>
    </div>

    <div class="person">
      <div class="person-name">Daniel Porter</div>
      <div class="person-title">Managing Director</div>
    </div>

    <div class="divider"></div>

    <div class="contact">
      <p class="contact-address">418 Maple Ridge Ave, #112<br>Fairview, OH 43210</p>
      <ul class="contact-list">
        <li><svg viewBox="0 0 24 24"><path d="M6.6 10.8a15.1 15.1 0 0 0 6.6 6.6l2.2-2.2a1 1 0 0 1 1-.25 11.4 11.4 0 0 0 3.6.57 1 1 0 0 1 1 1V20a1 1 0 0 1-1 1A17 17 0 0 1 3 4a1 1 0 0 1 1-1h3.5a1 1 0 0 1 1 1c0 1.25.2 2.45.57 3.57a1 1 0 0 1-.25 1z"/></svg>877-555-0142</li>
        <li><svg viewBox="0 0 24 24"><path d="M7 1h10a2 2 0 0 1 2 2v18a2 2 0 0 1-2 2H7a2 2 0 0 1-2-2V3a2 2 0 0 1 2-2zm0 3v14h10V4zm5 15.5a1.2 1.2 0 1 0 0 2.4 1.2 1.2 0 0 0 0-2.4z"/></svg>877-555-0198</li>
        <li><svg viewBox="0 0 24 24"><path d="M2 5h20v14H2zm2 2v.5l8 5 8-5V7zm0 2.8V17h16V9.8l-8 5z"/></svg>info@northcrestbuild.com</li>
        <li><svg viewBox="0 0 24 24"><path d="M12 2a10 10 0 1 0 0 20 10 10 0 0 0 0-20zm6.9 9h-3a15 15 0 0 0-1.3-5.6A8 8 0 0 1 18.9 11zM12 4.1c.9 1.3 1.8 3.6 1.9 6.9h-3.8c.1-3.3 1-5.6 1.9-6.9zM9.4 5.4A15 15 0 0 0 8.1 11h-3a8 8 0 0 1 4.3-5.6zM5.1 13h3a15 15 0 0 0 1.3 5.6A8 8 0 0 1 5.1 13zm6.9 6.9c-.9-1.3-1.8-3.6-1.9-6.9h3.8c-.1 3.3-1 5.6-1.9 6.9zm2.6-1.3a15 15 0 0 0 1.3-5.6h3a8 8 0 0 1-4.3 5.6z"/></svg>www.northcrestbuild.com</li>
      </ul>
    </div>

    <svg class="footer-bands" viewBox="0 0 560 320" aria-hidden="true">
      <polygon points="0,286 452,254 438,302 0,306" fill="var(--green)"/>
      <polygon points="470,248 560,242 560,300 454,300" fill="var(--black)"/>
    </svg>
  </section>

</main>
</body>
</html>
```